Construction material supplies company business card ****

1. Full company name “K T Masonry Works Ltd”
I am after a Business card design for the company as a whole. We are better known in Solomon Islands as “K T Masonry” for short.

We are a building materials supplier of
Ready Mixed Concrete, Bricks and Blocks,
Quarry products- gravel, aggregates, sand etc.
Cement distributor/retailer of reputable brands.
Other prefab concrete products. Culverts, wave breakers, concrete retaining blocks etc.

2. Competitive Advantage over Competition: Quality, efficient, professional, dependable, reliable

3. We want people to feel trust worthy, high quality, strong when they see our brand

5. No preference to color. Maybe more sturdy and corporate. Not fancy.

Industry/Entity Type

CONSTRUCTION SUPPLY

Contact Information for Business Card

Name, Position, office phone mob phone, email

Requirements
Must have
• the company logo
Nice to have
• would like to see a mixture of designs, of with logo only and also with simple graphic designs to bring out the company whilst still have the strong sturdy professional feeling

```html
<!DOCTYPE html>
<html lang="en">
<head>
<meta charset="utf-8">
<title>K T Masonry – Business Card</title>
<link href="https://fonts.googleapis.com/css2?family=Roboto:wght@400;500;700&display=swap" rel="stylesheet">
<style>
  :root{
    --backdrop:#2a2a2a;
    --navy:#1d426b;
    --navy-band:#244e7a;
    --card-light:#e9e9e9;
    --card-mid:#d3d3d3;
    --ink-light:#f2f4f7;
  }
  *{margin:0;padding:0;box-sizing:border-box}
  html,body{width:1200px;height:1138px;overflow:hidden}
  body{background:var(--backdrop);font-family:"Roboto",sans-serif;position:relative;color:var(--navy)}
  .card{position:absolute;left:274px;width:622px;height:375px;border-radius:16px;overflow:hidden;
    background:radial-gradient(ellipse at 40% 30%,var(--card-light),var(--card-mid))}
  .card--front{top:186px}
  .card--back{top:608px}

  .brand{position:absolute;display:flex;align-items:center;gap:18px}
  .brand__mark{background:var(--navy)}
  .brand__name{font-weight:700;color:var(--navy);letter-spacing:2px;white-space:nowrap;line-height:1}
  .card--front .brand{left:0;right:0;top:64px;justify-content:center}
  .card--front .brand__mark{width:66px;height:66px}
  .card--front .brand__name{font-size:56px}
  .card--back .brand{left:30px;top:40px}
  .card--back .brand__mark{width:54px;height:54px}
  .card--back .brand__name{font-size:46px}

  .band{position:absolute;left:0;right:0;top:214px;height:79px;background:var(--navy-band)}
  .pill{position:absolute;left:137px;top:186px;width:348px;height:41px;border-radius:21px;background:var(--navy);
    border:2px solid #e6e6e6;color:var(--ink-light);font-size:16px;display:flex;align-items:center;justify-content:center}
  .offer{position:absolute;left:0;right:0;text-align:center;font-size:16px;line-height:22px}
  .offer--band{top:239px;color:var(--ink-light)}
  .offer--plain{top:305px;line-height:24px}

  .person{position:absolute;left:37px;top:140px}
  .person__name{font-size:24px;font-weight:700}
  .person__role{font-size:17px;margin-top:4px}
  .address{position:absolute;right:36px;top:138px;text-align:right;font-size:16px;line-height:25px}
  .contacts{position:absolute;left:37px;top:222px;list-style:none;font-size:16.5px}
  .contacts li{display:flex;align-items:center;height:26px}
  .contacts svg{width:14px;height:14px;margin-right:10px;fill:var(--navy)}
  .wave{position:absolute;left:0;top:0;width:622px;height:375px}
  .values{position:absolute;right:36px;top:274px;text-align:right;color:var(--ink-light);font-size:16.5px;line-height:24px}
</style>
</head>
<body>
  <section class="card card--front">
    <div class="brand"><span class="brand__mark"></span><span class="brand__name">K T MASONRY</span></div>
    <div class="band"></div>
    <div class="pill">We are a building materials supplier of</div>
    <p class="offer offer--band">Ready Mixed Concrete, Bricks and Blocks, Quarry Products<br>Quarry Products:- Gravel, Aggregates, Sand Etc.</p>
    <p class="offer offer--plain">Cement Distributor/Retailer of Reputable Brands.<br>Other Concrete Products Culverts, Wave Breakers, Concrete Retaining Blocks</p>
  </section>

  <section class="card card--back">
    <svg class="wave" viewBox="0 0 622 375" aria-hidden="true">
      <path d="M0,300 C110,350 240,345 350,300 C450,258 530,232 622,236 L622,375 L0,375 Z" fill="var(--navy)"/>
      <path d="M0,322 C120,362 250,360 360,318 C300,350 150,362 40,318 Z" fill="#dcdcdc" opacity=".9"/>
      <path d="M0,338 C130,372 270,362 380,320 C280,372 120,378 0,352 Z" fill="#dcdcdc"/>
    </svg>
    <div class="brand"><span class="brand__mark"></span><span class="brand__name">K T MASONRY</span></div>
    <div class="person">
      <h1 class="person__name">Daniel Harlow</h1>
      <p class="person__role">Managing Director</p>
    </div>
    <p class="address">18 Harbour Road, Ranadi,<br>Honiara, Solomon Islands</p>
    <ul class="contacts">
      <li><svg viewBox="0 0 16 16"><path d="M2 5c0-2 2-3 6-3s6 1 6 3v1h-3V5H5v1H2z M4 7h8l2 7H2z"/></svg>000 0000 0000</li>
      <li><svg viewBox="0 0 16 16"><path d="M1 3h14v10H1z M2 4l6 5 6-5" stroke="#e3e3e3" stroke-width="1.2"/></svg>daniel@ktmasonry.com</li>
      <li><svg viewBox="0 0 16 16"><circle cx="8" cy="8" r="6.5" fill="none" stroke="var(--navy)" stroke-width="1.4"/><path d="M1.5 8h13M8 1.5c-3 3.5-3 9.5 0 13M8 1.5c3 3.5 3 9.5 0 13" fill="none" stroke="var(--navy)" stroke-width="1.2"/></svg>www.ktmasonry.com</li>
    </ul>
    <p class="values">Quality<br>Reliable &nbsp;|&nbsp; Professional<br>Efficient &nbsp;|&nbsp; Dependable</p>
  </section>
</body>
</html>
```